Summit Ridge Business Card

Side 1: Summit Ridge Logo (logo without Maltese cross) with industrial rope rescue related theme. Our company services - TRAINING - Fire Training, Confined Space Rescue Training, Rope Rescue training, Hazmat Training, Incident Command, EMS, Pump Operations Training. Website - summitridgeexample.com.
Side 2: Summit Ridge Fire Department Logo (logo with Maltese cross) with Firefighter related theme. Company (division) services - FIELD SERVICES - Fire Department, Stand-by Rescue, Safety, EMS, Planning. "Supporting the Emergency Response Community Since 1967"

Add contact information wherever it makes since (Name, Email, Phone).
I would like it to represent the Summit Ridge Fire Department Logo as a division not as a separate entity without saying it, possibly by depicting it in the background of Side 2 instead of being a standalone picture like the logo on Side 1.

```html
<!DOCTYPE html>
<html lang="en">
<head>
<meta charset="utf-8">
<title>Summit Ridge Business Card</title>
<link href="https://fonts.googleapis.com/css2?family=Open+Sans:wght@400;600;800&family=Lexend:wght@400&display=swap" rel="stylesheet">
<style>
  :root {
    --bg: #2c3038;
    --card: #ffffff;
    --red: #e8202a;
    --red-faint: rgba(232, 32, 42, 0.07);
    --black: #222222;
    --ink: #1d1d1d;
    --muted: #555555;
  }
  * { box-sizing: border-box; margin: 0; padding: 0; }
  html, body { width: 1200px; height: 780px; overflow: hidden; }
  body {
    background: var(--bg);
    font-family: "Open Sans", sans-serif;
    color: var(--ink);
    position: relative;
  }
  .card {
    position: absolute;
    width: 520px;
    height: 300px;
    background: var(--card);
    overflow: hidden;
    box-shadow: 0 14px 30px rgba(0,0,0,0.45);
  }
  .card--front { left: 50px; top: 240px; }
  .card--back { left: 630px; top: 240px; }

  .band-red {
    position: absolute; left: 0; right: 0; bottom: 0;
    height: 26px; background: var(--red);
  }
  .band-black {
    position: absolute; bottom: 26px; height: 14px; background: var(--black);
  }
  .card--front .band-black { left: 250px; right: 0; }
  .card--back .band-black { left: 0; width: 240px; }

  .brand {
    position: absolute;
    display: flex; align-items: center; gap: 10px;
    font-weight: 800;
    color: var(--red);
    letter-spacing: 2px;
    text-transform: uppercase;
    white-space: nowrap;
  }
  .brand-mark { background: var(--red); border-radius: 50%; flex: none; }

  .section-label {
    font-size: 10.5px; font-weight: 800; letter-spacing: 3px;
    text-transform: uppercase; color: var(--red);
  }
  .service-list {
    font-size: 11px; line-height: 17px; color: var(--muted);
  }

  /* Side 1 */
  .card--front .brand { left: 0; right: 0; top: 44px; justify-content: center; font-size: 34px; }
  .card--front .brand-mark { width: 22px; height: 22px; }
  .card--front .services {
    position: absolute; left: 50px; right: 50px; top: 112px; text-align: center;
  }
  .card--front .service-list { margin-top: 6px; }
  .card--front .web {
    position: absolute; left: 0; right: 0; top: 206px;
    text-align: center; font-size: 13px; color: var(--ink);
  }

  /* Side 2 */
  .division-backdrop {
    position: absolute; right: -70px; top: -60px;
    width: 260px; height: 260px; border-radius: 50%;
    background: var(--red-faint);
  }
  .person { position: absolute; left: 40px; top: 74px; text-align: right; width: 210px; }
  .person-name { font-family: "Lexend", sans-serif; font-size: 26px; color: var(--ink); white-space: nowrap; }
  .person-name .surname { color: var(--red); }
  .person-role { font-size: 11px; margin-top: 2px; }
  .divider {
    position: absolute; left: 276px; top: 70px; width: 1px; height: 80px; background: var(--ink);
  }
  .card--back .brand { left: 300px; top: 28px; font-size: 20px; }
  .card--back .brand-mark { width: 14px; height: 14px; }
  .contacts { position: absolute; left: 300px; top: 74px; list-style: none; }
  .contacts li {
    display: flex; align-items: center; gap: 8px;
    font-size: 11.5px; line-height: 22px; white-space: nowrap;
  }
  .contacts svg { width: 12px; height: 12px; fill: var(--red); flex: none; }
  .card--back .services { position: absolute; left: 40px; right: 30px; top: 172px; }
  .card--back .service-list { margin-top: 3px; }
  .tagline {
    position: absolute; left: 40px; right: 30px; top: 222px;
    font-size: 11px; font-weight: 600; color: var(--ink);
  }
</style>
</head>
<body>
  <section class="card card--front">
    <div class="brand"><span class="brand-mark"></span>Summit Ridge</div>
    <div class="services">
      <p class="section-label">Training</p>
      <p class="service-list">Fire Training · Confined Space Rescue Training · Rope Rescue Training · Hazmat Training · Incident Command · EMS · Pump Operations Training</p>
    </div>
    <p class="web">summitridgeexample.com</p>
    <div class="band-red"></div>
    <div class="band-black"></div>
  </section>

  <section class="card card--back">
    <div class="division-backdrop" role="img" aria-label="Faint Summit Ridge Fire Department emblem in the background"></div>
    <div class="person">
      <p class="person-name">Dana <span class="surname">Hollis</span></p>
      <p class="person-role">Director</p>
    </div>
    <div class="divider"></div>
    <div class="brand"><span class="brand-mark"></span>Summit Ridge</div>
    <ul class="contacts">
      <li>
        <svg viewBox="0 0 24 24" aria-hidden="true"><path d="M6.6 10.8a15.1 15.1 0 0 0 6.6 6.6l2.2-2.2a1 1 0 0 1 1-.25 11.4 11.4 0 0 0 3.6.57 1 1 0 0 1 1 1V20a1 1 0 0 1-1 1A17 17 0 0 1 3 4a1 1 0 0 1 1-1h3.5a1 1 0 0 1 1 1c0 1.25.2 2.45.57 3.57a1 1 0 0 1-.25 1z"/></svg>
        +1 555 010 0000
      </li>
      <li>
        <svg viewBox="0 0 24 24" aria-hidden="true"><path d="M2 5h20v14H2z M2 5l10 8 10-8" fill="none" stroke="#e8202a" stroke-width="2.4"/></svg>
        dh@ridgemail.co
      </li>
      <li>
        <svg viewBox="0 0 24 24" aria-hidden="true"><path d="M12 2l7 9h-4.5v11h-5V11H5z"/></svg>
        summitridgeexample.com
      </li>
    </ul>
    <div class="services">
      <p class="section-label">Field Services</p>
      <p class="service-list">Fire Department · Stand-by Rescue · Safety · EMS · Planning</p>
    </div>
    <p class="tagline">Supporting the Emergency Response Community Since 1967</p>
    <div class="band-red"></div>
    <div class="band-black"></div>
  </section>
</body>
</html>
```